real esate business card with company logo and name

we need a business card design for a real esate company

The company name is Walsh & Brand Pty Ltd, and we have our logo designed and will upload. We want classic or moden feel. Black or white background. looks more textured. Should include folowinginformations
Owen Walsh and Lucy Brand
Sales Agents & Onsite Manager
p: 07 5948 2063
F: 07 5948 2174
M:0431 857 219
3/42 Marlow Crescent, FERNLEA QLD 4213

We want this business card looks professonal. Thank you in advance.

Industry/Entity Type

Real Estate Agent

Contact Information for Business Card

Owen Walsh and Lucy Brand
Onsite Manager & Sales Agents
p: 07 5948 2063
M:0431 857 219

Font styles to use
Serif

Colors
000000
fbfbfb
333333
959595

Requirements
Must have
• company logo and name, black or white back ground

```html
<!DOCTYPE html>
<html lang="en">
<head>
<meta charset="utf-8">
<title>Walsh &amp; Brand Pty Ltd — Business Card</title>
<link href="https://fonts.googleapis.com/css2?family=Open+Sans:wght@400;600&family=Saira+Semi+Condensed:wght@400&display=swap" rel="stylesheet">
<style>
  :root {
    --black: #000000;
    --charcoal: #333333;
    --grey: #959595;
    --white: #fbfbfb;
    --backdrop: #d6d6d4;
    --rule: #4a4a4a;
  }
  * { margin: 0; padding: 0; box-sizing: border-box; }
  html, body {
    width: 1200px; height: 900px; overflow: hidden;
    background: var(--backdrop);
  }
  .canvas {
    position: relative; width: 1200px; height: 900px;
  }
  .card {
    position: absolute; left: 250px; width: 700px; height: 400px;
    overflow: hidden;
    background: radial-gradient(ellipse at 45% 35%, #1e1e1e 0%, #0b0b0b 55%, var(--black) 100%);
    color: var(--white);
    box-shadow: 0 6px 18px rgba(0,0,0,0.25);
  }
  .card--back { top: 34px; }
  .card--front { top: 466px; }

  .company-name {
    font-family: "Saira Semi Condensed", "Arial Narrow", sans-serif;
    font-weight: 400; text-transform: uppercase;
    letter-spacing: 1px; color: var(--grey);
    white-space: nowrap;
  }
  .card--back .company-name {
    position: absolute; left: 40px; right: 40px; top: 234px;
    text-align: center; font-size: 30px;
  }

  .brand {
    position: absolute; left: 180px; right: 40px; top: 72px;
    display: flex; align-items: center; gap: 18px;
  }
  .brand-mark {
    flex: none;
    width: 60px; height: 60px; background: var(--charcoal);
    border: 1px solid #555;
  }
  .card--front .company-name { font-size: 24px; color: #c9c9c9; }

  .agents {
    position: absolute; left: 40px; top: 168px;
    font-family: "Open Sans", Arial, sans-serif;
  }
  .agents-names { font-size: 19px; font-weight: 600; color: var(--grey); }
  .agents-role { font-size: 15px; color: var(--white); margin-top: 1px; }

  .divider {
    position: absolute; left: 340px; right: 60px; top: 242px;
    height: 1px; background: var(--rule);
  }

  .contact {
    position: absolute; right: 40px; top: 268px;
    font-family: "Open Sans", Arial, sans-serif;
    font-size: 16px; color: var(--white); text-align: right;
  }
  .contact-line {
    display: flex; justify-content: flex-end; align-items: center;
    gap: 10px; height: 24px;
  }
  .contact-line svg { width: 16px; height: 16px; fill: var(--grey); }
  .contact-address { margin-top: 12px; }
</style>
</head>
<body>
<main class="canvas">
  <section class="card card--back" aria-label="Card back">
    <p class="company-name">Walsh &amp; Brand Pty Ltd.</p>
  </section>

  <section class="card card--front" aria-label="Card front">
    <div class="brand">
      <span class="brand-mark"></span>
      <p class="company-name">Walsh &amp; Brand Pty Ltd.</p>
    </div>

    <div class="agents">
      <p class="agents-names">Owen Walsh and Lucy Brand</p>
      <p class="agents-role">Onsite Manager &amp; Sales Agents</p>
    </div>

    <div class="divider"></div>

    <div class="contact">
      <p class="contact-line">07 5948 2063
        <svg viewBox="0 0 16 16" aria-hidden="true"><path d="M2 5c0-2 2-3 6-3s6 1 6 3v1h-3V5H5v1H2zM4 7h8l2 6H2zM6 9v2h4V9z"/></svg>
      </p>
      <p class="contact-line">0431 857 219
        <svg viewBox="0 0 16 16" aria-hidden="true"><path d="M5 1h6a1 1 0 0 1 1 1v12a1 1 0 0 1-1 1H5a1 1 0 0 1-1-1V2a1 1 0 0 1 1-1zm0 2v9h6V3z"/></svg>
      </p>
      <p class="contact-address">3/42 Marlow Crescent FERNLEA QLD 4213</p>
    </div>
  </section>
</main>
</body>
</html>
```